Local Flower Farm Needs Business Card Design

I need business cards designed for a flower farm based in Eudora, Kansas.
Business Info:
We are a local cut flower farm located in Eudora, Kansas, founded by Corinne Haldwick. What started as a passion for agriculture and search for more joy in daily life has blossomed into a small business dedicated to providing the community with beautiful, fresh, and sustainable flowers. We specialize in local, seasonal blooms, ensuring that every petal reflects the care and dedication we pour into our craft. Our mission is to deliver the highest quality flowers directly to our customers through local farmers markets and to florists who share our commitment to sustainability. Join us in celebrating the beauty of nature, one bloom at a time!
Contact Details:
Corinne Haldwick
Owner
Phone 913-555-0147
Facebook: Rosalind Thorpe Gardens
Instagram: @RosalindThorpeGardens
Website: RosalindThorpeGardens.example
Target Market(s)
Wholesale to Florists and Direct to Consumer via Farmers Market
Industry/Entity Type
Florist, Farm
Contact Information for Business Card
Name, Contact Info, Logo
Look and feel
Each slider illustrates characteristics of the customer's brand and the style your logo design should communicate.

```html
<!DOCTYPE html>
<html lang="en">
<head>
<meta charset="utf-8">
<title>Rosalind Thorpe Gardens — Business Card</title>
<link rel="stylesheet" href="https://fonts.googleapis.com/css2?family=Arimo:wght@400;700&display=swap">
<style>
  :root {
    --backdrop: #d3d5d5;
    --card: #f7f7f6;
    --ink: #1d2422;
    --ink-soft: #4a4f4e;
    --rule: #3a3f3e;
    --faint: #e9eaea;
  }
  html, body {
    margin: 0;
    width: 1200px;
    height: 829px;
    overflow: hidden;
    background: var(--backdrop);
    font-family: "Arimo", Arial, sans-serif;
    color: var(--ink);
  }
  .canvas {
    position: relative;
    width: 1200px;
    height: 829px;
  }
  .card {
    position: absolute;
    top: 266px;
    width: 520px;
    height: 297px;
    background: var(--card);
    box-shadow: 0 2px 6px rgba(0,0,0,0.12);
    overflow: hidden;
  }
  .card--front { left: 60px; }
  .card--back  { left: 620px; }

  .brand {
    position: absolute;
    display: flex;
    align-items: center;
    justify-content: center;
    text-align: center;
    border: 1.5px solid var(--ink);
    border-radius: 50%;
    box-sizing: border-box;
  }
  .brand__name {
    font-weight: 700;
    text-transform: uppercase;
    letter-spacing: 0.08em;
    line-height: 1.25;
    color: var(--ink);
  }
  .card--front .brand {
    left: 258px; top: 22px; width: 112px; height: 112px;
  }
  .card--front .brand__name { font-size: 11px; }

  .person {
    position: absolute;
    left: 36px;
    top: 170px;
    width: 214px;
    text-align: right;
  }
  .person__name {
    margin: 0;
    font-size: 20px;
    font-weight: 700;
    letter-spacing: 0.01em;
    text-transform: uppercase;
  }
  .person__role {
    margin: 4px 0 0;
    font-size: 13px;
    color: var(--ink-soft);
  }
  .divider {
    position: absolute;
    left: 268px;
    top: 170px;
    width: 1.5px;
    height: 96px;
    background: var(--rule);
  }
  .contacts {
    position: absolute;
    left: 282px;
    top: 170px;
    margin: 0;
    padding: 0;
    list-style: none;
    font-size: 12.5px;
    color: var(--ink-soft);
  }
  .contacts li {
    display: flex;
    align-items: center;
    gap: 6px;
    height: 23px;
  }
  .contacts svg { flex: none; }

  .floral-wash {
    position: absolute;
    left: 40px;
    top: 0;
    width: 230px;
    height: 297px;
    background: linear-gradient(160deg, var(--faint), rgba(233,234,234,0.2));
  }
  .card--back .brand {
    left: 300px; top: 62px; width: 168px; height: 168px;
  }
  .card--back .brand__name { font-size: 15px; }
</style>
</head>
<body>
<main class="canvas">

  <section class="card card--front" aria-label="Card front">
    <div class="brand">
      <span class="brand__name">Rosalind<br>Thorpe<br>Gardens</span>
    </div>

    <div class="person">
      <h1 class="person__name">Corinne Haldwick</h1>
      <p class="person__role">Owner</p>
    </div>

    <div class="divider"></div>

    <ul class="contacts">
      <li>
        <svg width="11" height="11" viewBox="0 0 24 24" aria-hidden="true"><path fill="#1d2422" d="M6.6 10.8a15.1 15.1 0 0 0 6.6 6.6l2.2-2.2a1 1 0 0 1 1-.25 11.4 11.4 0 0 0 3.6.57 1 1 0 0 1 1 1V20a1 1 0 0 1-1 1A17 17 0 0 1 3 4a1 1 0 0 1 1-1h3.5a1 1 0 0 1 1 1c0 1.25.2 2.45.57 3.57a1 1 0 0 1-.25 1z"/></svg>
        913-555-0147
      </li>
      <li>
        <svg width="11" height="11" viewBox="0 0 12 12" aria-hidden="true"><circle cx="6" cy="6" r="5" fill="#1d2422"/></svg>
        Rosalind Thorpe Gardens
      </li>
      <li>
        <svg width="11" height="11" viewBox="0 0 12 12" aria-hidden="true"><rect x="1" y="1" width="10" height="10" rx="2" fill="none" stroke="#1d2422" stroke-width="1.4"/></svg>
        @RosalindThorpeGardens
      </li>
      <li>
        <svg width="11" height="11" viewBox="0 0 12 12" aria-hidden="true"><circle cx="6" cy="6" r="5" fill="#1d2422"/></svg>
        RosalindThorpeGardens.example
      </li>
    </ul>
  </section>

  <section class="card card--back" aria-label="Card back">
    <div class="floral-wash" role="img" aria-label="Faint line-drawn wildflower stems as a background decoration"></div>
    <div class="brand">
      <span class="brand__name">Rosalind<br>Thorpe<br>Gardens</span>
    </div>
  </section>

</main>
</body>
</html>
```